Redesign of agriculture and industrial webshop.

We are a chemical company that develops and produces all kinds of liquids. Cleaning products but also agriculture health products are our specialty. For both of them we have seperate webshops. www.brimfeldchemics.com/agriculture and www.brimfeldchemics.com/industrials. Both working with wordpress and visual composer to create the content. We'd like a modern and new professional redesign of the webshop to optimize sales and generating new clients. We have just redesigned our main page www.brimfeldchemics.com, this is not a webshop so it has different functions. But we'd like to take the choice of color to match the webshop colors. If you need any source documents, please let me know.

Target Market(s)

Agriculture market in the Netherlands and Industrials cleaning, lubrication market in The Netherlands

Industry/Entity Type

Agriculture

Number of Pages Required

2 page

Requirements
Must have
• Marketing strategies, colors, market segment, webshop look, webshop optimization for sales.
• Please design a homepages, product page, contact page and about us page for both webshops.

```html
<!DOCTYPE html>
<html lang="en">
<head>
<meta charset="utf-8">
<title>Brimfeld Chemics – Cleaning &amp; Lubrication</title>
<link href="https://fonts.googleapis.com/css2?family=Hind:wght@400;500;600&family=Roboto:wght@400;500;700&display=swap" rel="stylesheet">
<style>
:root{
  --topbar:#f1f1f1;
  --lang:#dcdcdc;
  --nav:#0f5b8a;
  --nav-active:#1f9ad6;
  --accent:#1fa8e0;
  --green:#6cae2e;
  --brand:#e0742a;
  --navy:#0b3a66;
  --service-top:#0e5f98;
  --service-bottom:#1676b8;
  --text:#555;
  --heading:#2a2a2a;
  --footer:#1ea0e2;
  --footer-bottom:#1789cf;
  --price:#0d5f93;
}
*{box-sizing:border-box;margin:0;padding:0}
html,body{width:1200px;height:2830px;overflow:hidden}
body{position:relative;font-family:"Roboto",sans-serif;color:var(--text);background:#fff}
.abs{position:absolute}
.heading{font-family:"Hind",sans-serif}

/* top bar */
.topbar{left:0;top:0;width:1200px;height:30px;background:var(--topbar);font-size:12px;color:#333}
.lang{left:181px;top:0;width:83px;height:30px;background:var(--lang);display:flex;align-items:center;justify-content:center;gap:6px}
.flag{width:18px;height:11px;background:#c8102e;border:2px solid #23408f}
.callus{left:320px;top:8px}
.callus b{font-weight:400;color:var(--green)}
.account-links{left:785px;top:8px}

/* header */
.header{left:0;top:30px;width:1200px;height:108px;background:#fff}
.logo{left:185px;top:55px;font-family:"Hind",sans-serif;font-weight:600;font-size:44px;line-height:56px;color:var(--brand);letter-spacing:1px}
.search{left:449px;top:72px;width:327px;height:34px;border:2px solid #bbb;display:flex;align-items:center;padding-left:12px;gap:8px;font-size:13px;color:#888}
.cart{left:898px;top:72px;display:flex;align-items:center;gap:10px;font-size:16px;color:#333}

/* nav */
.nav{left:0;top:138px;width:1200px;height:45px;background:var(--nav);display:flex;align-items:center;padding-left:179px}
.nav a{color:#fff;text-decoration:none;font-size:12px;font-weight:700;padding:0 14px;height:45px;line-height:45px}
.nav a.active{background:var(--nav-active);width:85px;text-align:center;margin-right:9px}

/* hero */
.hero{left:0;top:183px;width:1200px;height:568px}
.hero-img{left:0;top:0;width:1200px;height:568px;background:linear-gradient(180deg,#0f0b06 0%,#2a1c08 55%,#6a4810 100%)}
.hero-title{left:0;top:158px;width:1200px;text-align:center;color:#fff;font-family:"Hind",sans-serif}
.hero-title .small{font-size:32px;font-weight:500;line-height:40px}
.hero-title .big{font-size:44px;font-weight:600;line-height:52px;letter-spacing:1px}
.btn{background:var(--accent);color:#fff;border-radius:22px;text-align:center;font-weight:500}
.hero-btn{left:517px;top:262px;width:166px;height:44px;line-height:44px;font-size:17px}
.dots{left:1073px;top:201px;display:flex;flex-direction:column;gap:9px}
.dots span{width:12px;height:12px;border-radius:50%;background:#fff}
.dots span.on{background:transparent;border:2px solid #fff}

/* who we are */
.who{left:0;top:751px;width:1200px;height:406px;background:linear-gradient(90deg,#f6f5f3,#eeece8)}
.who-photo{left:189px;top:25px;width:366px;height:366px;border-radius:50%;background:radial-gradient(circle,#c9b49a,#9b8a74);border:14px solid #cfc7b3}
.who-title{left:600px;top:58px;font-size:34px;font-weight:500;color:var(--heading);letter-spacing:1px}
.who-text{left:604px;top:113px;width:450px;font-size:16px;line-height:25px;color:#555}
.who-btn{left:604px;top:304px;width:160px;height:41px;line-height:41px;font-size:16px}

/* services */
.services{left:0;top:1208px;width:1200px;height:496px;background:linear-gradient(var(--service-top),var(--service-bottom))}
.section-title{width:1200px;text-align:center;font-family:"Hind",sans-serif;font-weight:500;font-size:33px;letter-spacing:1px}
.services .section-title{top:42px;color:#fff}
.service{top:113px;width:217px;height:264px;border-radius:50%;background:var(--navy);color:#fff;text-align:center;padding:0 28px}
.service svg.icon{margin-top:45px}
.service h3{font-family:"Hind",sans-serif;font-weight:500;font-size:18px;margin-top:4px;letter-spacing:.5px}
.service p{font-size:9px;line-height:14px;color:#9fb8d6;margin-top:10px}
.service .chev{margin-top:12px}

/* products */
.products .section-title{top:1746px;color:var(--heading)}
.tabs{left:0;top:1805px;width:1200px;display:flex;justify-content:center;gap:44px;font-family:"Hind",sans-serif;font-weight:600;font-size:16px;color:#222}
.tabs span.active{border-bottom:3px solid var(--green);padding-bottom:3px}
.card{top:1891px;width:199px;height:339px;background:#fff;box-shadow:0 0 6px rgba(0,0,0,.3);text-align:center;z-index:2}
.bottle{width:100px;height:130px;margin:22px auto 0;border-radius:10px 10px 6px 6px}
.card h4{font-family:"Hind",sans-serif;font-weight:500;color:var(--accent);font-size:19px;margin-top:26px}
.card p{font-size:12px;line-height:17px;color:#888;padding:0 20px;margin-top:2px}
.card .price{font-family:"Hind",sans-serif;font-weight:600;color:var(--price);font-size:23px;margin-top:10px}
.card .btn{width:126px;height:31px;line-height:31px;font-size:14px;margin:8px auto 0}
.arrow{top:2025px}

/* shipping */
.shipping{left:0;top:2180px;width:1200px;height:343px;background:linear-gradient(90deg,#b7bcbf,#d8d6d1 45%,#a9b4bd)}
.ship-text{left:0;top:128px;width:1200px;text-align:center;color:#222;font-family:"Hind",sans-serif}
.ship-text .big{font-size:46px;font-weight:500;line-height:52px;letter-spacing:1px}
.ship-text .small{font-size:31px;line-height:40px;letter-spacing:1px}

/* footer */
.footer{left:0;top:2523px;width:1200px;height:260px;background:var(--footer);color:#fff}
.fcol{top:57px}
.fcol h5{font-family:"Hind",sans-serif;font-weight:600;font-size:15px;letter-spacing:.5px;margin-bottom:12px}
.fcol li{list-style:none;font-size:13px;line-height:25px}
.news p{font-size:13px}
.news .input{margin-top:10px;width:224px;height:34px;border:1.5px solid #fff;font-size:11px;line-height:31px;padding-left:14px}
.news .sub{margin-top:15px;width:119px;height:28px;line-height:28px;background:var(--navy);font-size:12px;font-weight:700;text-align:center}
.social{display:flex;gap:8px}
.social span{width:30px;height:30px;border-radius:50%;border:1.5px solid #fff}
.pay{display:flex;gap:7px;margin-top:15px}
.pay span{width:31px;height:15px;background:#fff;border-radius:2px}
.copyright{left:0;top:2783px;width:1200px;height:47px;background:var(--footer-bottom);color:#fff;font-size:12px;text-align:center;line-height:47px}
</style>
</head>
<body>

<div class="abs topbar">
  <div class="abs lang"><span class="flag"></span>ENG
    <svg width="9" height="6" viewBox="0 0 9 6"><path d="M1 1l3.5 3.5L8 1" fill="none" stroke="#333" stroke-width="1.3"/></svg></div>
  <div class="abs callus">
    <svg width="12" height="12" viewBox="0 0 24 24" style="vertical-align:-2px"><path d="M6.6 10.8a15 15 0 006.6 6.6l2.2-2.2c.3-.3.7-.4 1-.2 1.1.4 2.3.6 3.6.6.6 0 1 .4 1 1V20c0 .6-.4 1-1 1A17 17 0 013 4c0-.6.4-1 1-1h3.5c.6 0 1 .4 1 1 0 1.3.2 2.5.6 3.6.1.3 0 .7-.2 1z" fill="#1fa8e0"/></svg>
    CALL US <b>+31 400 12 34 56</b></div>
  <div class="abs account-links">My Account &nbsp;|&nbsp; Wishlist &nbsp;|&nbsp; Login &nbsp;|&nbsp; Checkout</div>
</div>

<div class="abs header"></div>
<div class="abs logo">BRIMFELD</div>
<div class="abs search">
  <svg width="15" height="15" viewBox="0 0 16 16"><circle cx="6.5" cy="6.5" r="5" fill="none" stroke="#666" stroke-width="2"/><path d="M10 10l5 5" stroke="#666" stroke-width="2"/></svg>
  Search here...</div>
<div class="abs cart">
  <svg width="34" height="28" viewBox="0 0 34 28"><path d="M3 9h28l-4 17H7z" fill="#1676b8"/><path d="M10 9l5-7M24 9l-5-7" stroke="#1676b8" stroke-width="2.5" fill="none"/><path d="M10 13v9M15 13v9M20 13v9M25 13v9" stroke="#fff" stroke-width="1.5"/></svg>
  0 ITEMS</div>

<nav class="abs nav">
  <a class="active">HOME</a><a>ABOUT US</a><a>CLEANING</a><a>LUBRICATION</a><a>DISINFECTION</a><a>PRESERVATION</a><a>KNOWLEDGE</a><a>PACKAGING</a><a>CONTACT</a>
</nav>

<section class="abs hero">
  <div class="abs hero-img" role="img" aria-label="Golden oil drop falling into a glossy pool of lubricant"></div>
  <div class="abs hero-title"><div class="small">WELCOME TO BRIMFELD</div><div class="big">CLEANING &amp; LUBRICATION</div></div>
  <div class="abs btn hero-btn">Shop Now</div>
  <div class="abs dots"><span class="on"></span><span></span><span></span><span></span></div>
</section>

<section class="abs who">
  <div class="abs who-photo" role="img" aria-label="Two workers in hard hats reviewing a tablet on site"></div>
  <h2 class="abs heading who-title">WHO WE ARE</h2>
  <p class="abs who-text">Brimfeld Chemics develops and produces specialist maintenance products for the food and non-food industry. The purpose of using these products is to save on both production and labor costs. These products have been developed with the most important criteria; effectiveness and safety. Safe for the user, the material and, if necessary, for food and the environment.</p>
  <div class="abs btn who-btn">Learn More</div>
</section>

<section class="abs services">
  <h2 class="abs section-title">OUR SERVICES</h2>
  <div class="abs service" style="left:156px">
    <svg class="icon" width="52" height="46" viewBox="0 0 52 46" fill="none" stroke="#fff" stroke-width="2"><path d="M6 14h40l-5 28H11z"/><path d="M6 14c8 6 16-2 20 2s12-4 20-2"/><path d="M18 10l10-8 8 10"/></svg>
    <h3>CLEANING</h3>
    <p>Lorem ipsum dolor sit amet consectetur adipiscing elit sed do eiusmod tempor incididunt ut</p>
    <svg class="chev" width="32" height="32" viewBox="0 0 32 32"><circle cx="16" cy="16" r="14" fill="none" stroke="#fff" stroke-width="1.5"/><path d="M10 13l6 6 6-6" fill="none" stroke="#fff" stroke-width="1.5"/></svg>
  </div>
  <div class="abs service" style="left:377px">
    <svg class="icon" width="52" height="46" viewBox="0 0 52 46" fill="none" stroke="#fff" stroke-width="2"><rect x="10" y="16" width="24" height="26"/><path d="M16 16V8h12v8M22 8V3M34 22l10-4v8"/><path d="M46 32c0 3-2 5-3 5s-3-2-3-5l3-5z"/></svg>
    <h3>LUBRICATION</h3>
    <p>Lorem ipsum dolor sit amet consectetur adipiscing elit sed do eiusmod tempor incididunt ut</p>
    <svg class="chev" width="32" height="32" viewBox="0 0 32 32"><circle cx="16" cy="16" r="14" fill="none" stroke="#fff" stroke-width="1.5"/><path d="M10 13l6 6 6-6" fill="none" stroke="#fff" stroke-width="1.5"/></svg>
  </div>
  <div class="abs service" style="left:594px">
    <svg class="icon" width="52" height="46" viewBox="0 0 52 46" fill="none" stroke="#fff" stroke-width="2"><circle cx="26" cy="23" r="12"/><circle cx="22" cy="20" r="2"/><circle cx="30" cy="26" r="2"/><path d="M26 11V3M26 35v8M14 23H6M38 23h8M17 14l-5-5M35 32l5 5M35 14l5-5M17 32l-5 5"/></svg>
    <h3>DISINFECTION</h3>
    <p>Lorem ipsum dolor sit amet consectetur adipiscing elit sed do eiusmod tempor incididunt ut</p>
    <svg class="chev" width="32" height="32" viewBox="0 0 32 32"><circle cx="16" cy="16" r="14" fill="none" stroke="#fff" stroke-width="1.5"/><path d="M10 13l6 6 6-6" fill="none" stroke="#fff" stroke-width="1.5"/></svg>
  </div>
  <div class="abs service" style="left:813px">
    <svg class="icon" width="52" height="46" viewBox="0 0 52 46" fill="none" stroke="#fff" stroke-width="2"><ellipse cx="26" cy="6" rx="14" ry="4"/><path d="M12 6v34c0 2 6 4 14 4s14-2 14-4V6"/><circle cx="26" cy="23" r="6"/></svg>
    <h3>PRESERVATION</h3>
    <p>Lorem ipsum dolor sit amet consectetur adipiscing elit sed do eiusmod tempor incididunt ut</p>
    <svg class="chev" width="32" height="32" viewBox="0 0 32 32"><circle cx="16" cy="16" r="14" fill="none" stroke="#fff" stroke-width="1.5"/><path d="M10 13l6 6 6-6" fill="none" stroke="#fff" stroke-width="1.5"/></svg>
  </div>
</section>

<section class="products">
  <h2 class="abs section-title">OUR PRODUCTS</h2>
  <div class="abs tabs"><span class="active">CLEANING</span><span>LUBRICATION</span><span>DISINFECTION</span><span>CONSERVATION</span></div>
  <div class="abs arrow" style="left:145px"><svg width="26" height="52" viewBox="0 0 26 52"><path d="M24 2L3 26l21 24" fill="none" stroke="#999" stroke-width="2"/></svg></div>
  <div class="abs arrow" style="left:1042px"><svg width="26" height="52" viewBox="0 0 26 52"><path d="M2 2l21 24L2 50" fill="none" stroke="#999" stroke-width="2"/></svg></div>
</section>

<section class="abs shipping" role="img" aria-label="Delivery person handing over a cardboard parcel, muted tones">
  <div class="abs ship-text"><div class="big">FREE SHIPPING</div><div class="small">FOR ORDERS&gt; € 200 EXCL. VAT</div></div>
</section>

<div class="abs card" style="left:192px">
  <div class="bottle" role="img" aria-label="Blue jerrycan of cleaning liquid" style="background:linear-gradient(#a9d4ee,#4ea6da)"></div>
  <h4>PRODUCT NAME</h4><p>Fusce tellus Sed metus augue convallis et vehicula</p><div class="price">£357.50</div><div class="btn">Shop Now</div>
</div>
<div class="abs card" style="left:402px">
  <div class="bottle" role="img" aria-label="Pale yellow jerrycan of cleaning liquid" style="background:linear-gradient(#f7f3c8,#e6dd8a)"></div>
  <h4>PRODUCT NAME</h4><p>Fusce tellus Sed metus augue convallis et vehicula</p><div class="price">£357.50</div><div class="btn">Shop Now</div>
</div>
<div class="abs card" style="left:610px">
  <div class="bottle" role="img" aria-label="Blue jerrycan of cleaning liquid" style="background:linear-gradient(#a9d4ee,#4ea6da)"></div>
  <h4>PRODUCT NAME</h4><p>Fusce tellus Sed metus augue convallis et vehicula</p><div class="price">£357.50</div><div class="btn">Shop Now</div>
</div>
<div class="abs card" style="left:819px">
  <div class="bottle" role="img" aria-label="White jerrycan of cleaning liquid" style="background:linear-gradient(#f7f7f7,#d4d4d4)"></div>
  <h4>PRODUCT NAME</h4><p>Fusce tellus Sed metus augue convallis et vehicula</p><div class="price">£357.50</div><div class="btn">Shop Now</div>
</div>

<footer class="abs footer">
  <div class="abs fcol news" style="left:172px">
    <h5>SIGN UP NEWSLETTER</h5>
    <p>Please sign up for newsletter</p>
    <div class="input">Email address</div>
    <div class="sub">SUBSCRIBE</div>
  </div>
  <div class="abs fcol" style="left:457px"><h5>COMPANY</h5><ul><li>Home</li><li>About Us</li><li>Our Producs</li><li>Cattle</li></ul></div>
  <div class="abs fcol" style="left:579px"><h5>PRODUCTS</h5><ul><li>Poultry</li><li>Crop</li><li>Auxiliary Prouducts</li><li>Knowledge</li></ul></div>
  <div class="abs fcol" style="left:725px"><h5>RESOURCES</h5><ul><li>My Account</li><li>Cart</li><li>Support</li><li>Contact Us</li></ul></div>
  <div class="abs fcol" style="left:849px"><h5>FOLLOW US</h5>
    <div class="social"><span></span><span></span><span></span><span></span></div>
    <div class="pay"><span></span><span></span><span></span><span></span><span></span></div>
  </div>
</footer>
<div class="abs copyright">© 2018 Company Name. All right reserved</div>

</body>
</html>
```